Web Design Project

Psychotherapy and Counselling Practice needs a landing page web design.

My business "Larkfield Advisory" specialises in the treatment of Anxiety and Depression with a holistic approach, endeavouring to unlock the key that holds us to ransom in a life that is imbalanced, frustrating, and ultimately of our own making due to our own perceptions and behaviours.

There is much that impacts us which we cannot change, but we are always in control of how we think, and how we frame our experiences.....learning to challenge those thoughts and behaviours that are destructive and disempowering opens up a world of joyful possibility. Life is about making choices, learn to make wiser and healthier choices.......

Larkfield Advisory has a client base of individual clients but will seek to expand to offer services to the Corporate world by offering an adjunct to employers for established "Wellness Programs".

Larkfield Advisory is a highly professional, ethically bound business, with the needs of the client at the forefront of all we do.

Larkfield Advisory wishes to avoid the usual "jargon driven" psychobabble offered on many counselling web pages. It aims to be stylishly presented, clean in look and with as few "words" as possible and a largely white background (faster loading and more powerful impact of what is stated), those words contained in the webpage should be meaningful, persuasive and have an impact simply at glance. Larkfield does not want , or expect, those prospective clients in need of support , to be reading through volumes of industry driven cliches.

At this point Larkfield is just looking for a high quality landing page. However in time this will likely expand to include other sections such as case studies, video content etc.

Target Market(s)

Those in need of emotional support, suffering mental health issues, and those simply wanting to become self aware supported by a mindful therapist.

Industry/Entity Type

Industry

Requirements
Must have
• The design must incorporate the Larkfield logo and colour schemes found on the attached files.

```html
<!DOCTYPE html>
<html lang="en">
<head>
<meta charset="utf-8">
<title>Larkfield Advisory</title>
<link rel="stylesheet" href="https://fonts.googleapis.com/css2?family=Lato:wght@400;700;900&display=swap">
<style>
:root{
  --bg-center:#ffffff;
  --bg-edge:#e6e6e6;
  --green:#86a812;
  --green-soft:#b6cf5a;
  --tile:#6b6b6b;
  --tile-dark:#555555;
  --nav-text:#6e6e6e;
  --pill:#6a6a6a;
  --white:#ffffff;
  --foot-text:#8a8a8a;
}
*{margin:0;padding:0;box-sizing:border-box}
html,body{width:1200px;height:617px;overflow:hidden}
body{
  position:relative;
  font-family:"Lato",sans-serif;
  background:radial-gradient(ellipse 520px 360px at 600px 300px,var(--bg-center) 40%,var(--bg-edge) 100%);
}
.brand{
  position:absolute;left:0;width:1200px;top:74px;text-align:center;
  font-size:30px;font-weight:400;letter-spacing:1px;color:var(--green);
}
.main-nav{position:absolute;top:130px;left:0;width:1200px;height:18px}
.main-nav a{
  position:absolute;top:0;height:18px;line-height:18px;
  font-size:12.5px;color:var(--nav-text);text-decoration:none;white-space:nowrap;
}
.main-nav a.is-active{
  background:var(--pill);color:var(--white);border-radius:4px;padding:0 6px;
}
.divider{position:absolute;display:block}
.divider path{fill:var(--green)}
.feature{
  position:absolute;top:226px;width:160px;height:159px;
  border-radius:44%;
  background:radial-gradient(ellipse at 50% 35%,var(--tile) 55%,var(--tile-dark) 100%);
  box-shadow:0 10px 14px -6px rgba(0,0,0,.28);
  color:var(--white);text-align:center;
}
.feature h2{
  margin-top:27px;font-size:21px;font-weight:900;letter-spacing:-1px;line-height:1;
}
.feature p{
  margin:13px auto 0;width:142px;font-size:11.4px;line-height:12.8px;
}
.feature .more{
  position:absolute;left:0;width:100%;top:133px;
  font-size:11.5px;font-weight:700;color:var(--white);text-decoration:none;
}
.sprig{
  position:absolute;left:446px;top:246px;width:42px;height:72px;
  border-radius:20px;
  background:radial-gradient(ellipse at 50% 50%,rgba(134,168,18,.35),rgba(134,168,18,0) 70%);
}
.social{position:absolute;top:443px;left:559px;display:flex;gap:2.5px}
.social a{
  display:block;width:18.5px;height:18.5px;border-radius:5px;background:var(--green);
  box-shadow:0 2px 3px rgba(0,0,0,.2);
}
.copyright{
  position:absolute;top:512px;left:0;width:1200px;text-align:center;
  font-size:10px;color:var(--foot-text);
}
.copyright strong{color:#777}
</style>
</head>
<body>
  <header>
    <div class="brand">LARKFIELD</div>
    <nav class="main-nav">
      <a class="is-active" href="#" style="left:354px">HOME</a>
      <a href="#" style="left:415px">ABOUT US</a>
      <a href="#" style="left:491px">TREATMENTS</a>
      <a href="#" style="left:644px">SERIVCES</a>
      <a href="#" style="left:716px">CASE STUDIES</a>
      <a href="#" style="left:811px">CONTACT US</a>
    </nav>
    <svg class="divider" style="left:269px;top:157px" width="664" height="16" viewBox="0 0 664 16">
      <path d="M0 2 C200 1 300 4 332 6 C364 4 464 1 664 2 C464 4 364 9 332 16 C300 9 200 4 0 2Z"/>
    </svg>
  </header>

  <main>
    <section class="feature" style="left:286px">
      <h2>ABOUT US</h2>
      <p>Larkfield Advisory is a highly professional, ethically bound business, with the needs of the client at the forefront of all we do.</p>
      <a class="more" href="#">Read More..</a>
    </section>
    <div class="sprig" role="img" aria-label="Small climbing vine sprig decoration"></div>

    <section class="feature" style="left:514px">
      <h2>TREATMENTS</h2>
      <p>Treatment of Anxiety and Depression with holistic approach, endeavouring to unloack the key that holds us ransom in a life.</p>
      <a class="more" href="#">Read More..</a>
    </section>

    <section class="feature" style="left:742px">
      <h2>SERVICES</h2>
      <p>Psychotherapy &amp; Counselling Practice, Wellness Programs, Individual clients, Corporate services</p>
      <a class="more" href="#">Read More..</a>
    </section>
  </main>

  <footer>
    <div class="social">
      <a href="#" aria-label="Social link 1"></a>
      <a href="#" aria-label="Social link 2"></a>
      <a href="#" aria-label="Social link 3"></a>
      <a href="#" aria-label="Social link 4"></a>
    </div>
    <svg class="divider" style="left:272px;top:484px" width="666" height="16" viewBox="0 0 666 16">
      <path d="M0 14 C200 13 300 9 333 1 C366 9 466 13 666 14 C466 12 366 10 333 16 C300 10 200 12 0 14Z"/>
    </svg>
    <div class="copyright"><strong>© 2013</strong> LARKFIELD</div>
  </footer>
</body>
</html>
```